Website Design for R W Builders: Showcasing Excellence in General Contracting

R W Builders, a leading general contractor based in California, is seeking a professional and engaging website design to effectively showcase our expertise, services, and commitment to excellence. The website will serve as a digital platform to represent our brand identity, highlight our portfolio, and attract potential clients in various sectors.

Key Objectives:

Reflect Company Identity: The website should accurately reflect the identity and values of R W Builders, including our dedication to quality, professionalism, and client satisfaction.
Showcase Services: Highlight our wide range of general contracting services, including but not limited to construction management, design-build, renovation, and commercial construction.
Portfolio Display: Display an extensive portfolio of past projects completed by R W Builders, showcasing our capabilities, craftsmanship, and successful outcomes.
Client Testimonials: Incorporate client testimonials and case studies to demonstrate our track record of delivering projects on time, within budget, and to the highest standards.
Contact Information: Ensure easy access to contact information, including phone number, email, and physical address, to facilitate communication with potential clients.
Responsive Design: Develop a responsive website design optimized for various devices and screen sizes, ensuring a seamless user experience across desktops, laptops, tablets, and smartphones.
Search Engine Optimization (SEO): Implement SEO best practices to enhance the visibility of the website on search engines, increasing organic traffic and generating leads.
User-Friendly Navigation: Create an intuitive and user-friendly navigation structure that enables visitors to easily find the information they need, such as services, portfolio, testimonials, and contact details.
Visual Appeal: Utilize visually appealing graphics, images, and layout designs to capture the attention of visitors and leave a lasting impression of professionalism and quality.
Compliance and Security: Ensure compliance with industry standards and regulations, as well as implementing necessary security measures to protect user data and privacy.

```html
<!DOCTYPE html>
<html lang="en">
<head>
<meta charset="utf-8">
<title>R W Builders — General Contracting</title>
<link href="https://fonts.googleapis.com/css2?family=Roboto+Condensed:wght@700;800&family=Roboto:wght@400;500;700&display=swap" rel="stylesheet">
<style>
:root{
  --orange:#e2531c;
  --gold:#e2b414;
  --ink:#111111;
  --text:#6a6a6a;
  --paper:#ffffff;
  --mist:#f4f4f4;
  --grad:linear-gradient(90deg,var(--orange),var(--gold));
}
*{box-sizing:border-box;margin:0;padding:0}
html,body{width:1200px;height:4505px;overflow:hidden;background:var(--paper)}
body{position:relative;font-family:'Roboto',sans-serif;color:var(--ink)}
.abs{position:absolute}
.head{font-family:'Roboto Condensed',sans-serif;font-weight:800;font-size:42px;line-height:1;color:var(--ink)}
.head .dash{display:inline-block;width:24px;height:3px;background:currentColor;vertical-align:middle;margin:0 12px}
.btn{position:absolute;height:42px;border-radius:21px;background:var(--grad);color:#fff;font-size:13px;font-weight:700;display:flex;align-items:center;justify-content:center;gap:6px;letter-spacing:.2px}
.btn i{display:inline-block;width:12px;height:12px;border-radius:50%;background:#fff;position:relative}
.btn i:after{content:"";position:absolute;left:3px;top:3.5px;border-left:5px solid var(--orange);border-top:2.5px solid transparent;border-bottom:2.5px solid transparent}
.photo{position:absolute}
/* nav */
.nav{left:0;top:0;width:1200px;height:75px;background:var(--paper);z-index:3}
.nav a{position:absolute;top:29px;font-size:14px;font-weight:500;color:var(--ink);text-decoration:none}
.brand{left:61px;top:-18px;width:202px;height:202px;border-radius:50%;background:var(--paper);z-index:4;display:flex;align-items:center;justify-content:center;flex-direction:column}
.brand span{font-family:'Roboto Condensed',sans-serif;font-weight:800;font-size:26px;color:var(--ink);line-height:1.05;text-align:center}
/* hero */
.hero-title{left:0;width:1200px;text-align:center;z-index:2}
/* cards */
.svc{position:absolute;width:219px;height:302px;border-radius:34px;border:3px solid #fff;box-shadow:0 4px 14px rgba(0,0,0,.15);overflow:hidden}
.svc .tag{position:absolute;left:12px;right:12px;bottom:16px;height:46px;border-radius:23px;background:#fff;display:flex;align-items:center;justify-content:center;font-weight:700;font-size:15px;box-shadow:0 2px 6px rgba(0,0,0,.15)}
.arrow{position:absolute;width:34px;height:34px;border-radius:50%;background:#fff;box-shadow:0 2px 6px rgba(0,0,0,.12);display:flex;align-items:center;justify-content:center;font-size:16px;font-weight:700}
/* experience */
.exp{position:absolute;width:230px;text-align:center;color:#fff;font-weight:700;font-size:16px;line-height:28px}
.exp svg{display:block;margin:28px auto 0}
/* testimonials */
.quote{position:absolute;width:278px;height:122px;background:#fff;border-radius:0 30px 30px 30px;padding:16px 20px 0 50px}
.quote.lift{box-shadow:4px 6px 10px rgba(0,0,0,.18)}
.quote b{font-size:15px;font-weight:700}
.quote .stars{color:#f3a51c;font-size:13px;letter-spacing:2px;margin-left:18px}
.quote p{font-size:13px;color:var(--text);line-height:25px;margin-top:4px}
.avatar{position:absolute;width:66px;height:66px;border-radius:50%;border:3px solid #fff;box-shadow:0 0 0 2px var(--orange);background:linear-gradient(160deg,#c9a27d,#6d5a48)}
/* form */
.field{position:absolute;background:#fff;border-radius:22px;font-size:10px;color:#555;padding:18px 24px;letter-spacing:.4px}
/* footer */
.fcol{position:absolute;color:#fff;font-size:13px;line-height:30px}
.fcol h4{font-size:14px;font-weight:700;margin-bottom:12px;line-height:1}
</style>
</head>
<body>

<!-- navigation -->
<header class="abs nav">
  <a style="left:498px">Home</a>
  <a style="left:574px">About</a>
  <a style="left:649px">Services</a>
  <a style="left:740px">Testimonial</a>
  <a style="left:854px">Portfolio</a>
  <div class="btn" style="left:953px;top:14px;width:135px;height:44px;border-radius:22px;font-size:12px">CONTACT US</div>
</header>
<div class="abs brand"><span>R W<br>BUILDERS</span><span style="font-size:13px;font-family:'Roboto',sans-serif;font-weight:700;margin-top:6px">OAKRIDGE, CA</span></div>

<!-- hero -->
<svg class="abs" style="left:0;top:75px" width="1200" height="790" viewBox="0 0 1200 790" aria-hidden="true">
  <defs><linearGradient id="heroBand" x1="0" x2="1"><stop offset="0" stop-color="#e2531c"/><stop offset="1" stop-color="#e2b414"/></linearGradient>
  <linearGradient id="heroSky" x1="0" y1="0" x2="1" y2="1"><stop offset="0" stop-color="#d9c9ae"/><stop offset=".5" stop-color="#b9865a"/><stop offset="1" stop-color="#5a4632"/></linearGradient></defs>
  <polygon points="0,0 1200,0 1200,564 0,777" fill="url(#heroSky)"/>
  <polygon points="0,760 1200,545 1200,564 0,790" fill="url(#heroBand)"/>
</svg>
<div class="photo" role="img" aria-label="Three construction workers in hard hats and safety vests reviewing plans on a building site at sunset" style="left:0;top:75px;width:1200px;height:560px"></div>
<div class="abs hero-title" style="top:142px;font-size:21px;font-weight:500">WELCOME TO</div>
<div class="abs hero-title head" style="top:196px;font-size:80px">R W BUILDERS</div>
<div class="btn" style="left:530px;top:563px;width:131px;height:42px;font-size:13px">GET STARTED <i></i></div>

<!-- about -->
<div class="abs" style="left:184px;top:918px;width:306px;height:303px;display:flex;align-items:center;justify-content:center">
  <span class="head" style="font-size:56px;text-align:center">R W<br>BUILDERS</span>
</div>
<h2 class="abs head" style="left:602px;top:872px">About us<span class="dash"></span></h2>
<div class="abs" style="left:602px;top:946px;width:486px;font-size:13px;line-height:25.7px;color:var(--text);text-align:justify">
  <p>With vast experience in the trades, site superintendence, safety, quality control, and all aspects of general contracting, R W Builders can plan, manage and execute building construction projects in all sizes under any delivery method: design-build, CM at Risk, or design-bid-build.</p>
  <p style="margin-top:22px">R W Builders engages in horizontal construction (NAICS 237990) primarily with the county, state, public work, and federal municipalities under Job Order (JOC) type contracting vehicles.</p>
</div>
<div class="btn" style="left:602px;top:1175px;width:134px">LEARN MORE <i></i></div>

<!-- services -->
<svg class="abs" style="left:0;top:1210px" width="1200" height="1345" viewBox="0 0 1200 1345" aria-hidden="true">
  <defs><linearGradient id="expBand" x1="0" x2="1"><stop offset="0" stop-color="#e2531c"/><stop offset="1" stop-color="#e2b414"/></linearGradient></defs>
  <polygon points="0,260 1200,6 1200,1345 0,1345" fill="#f4f4f4"/>
  <polygon points="411,184 1200,0 1200,44" fill="url(#expBand)"/>
  <polygon points="0,872 1200,668 1200,1135 0,1338" fill="url(#expBand)"/>
  <polygon points="0,860 640,742 0,866" fill="#ffffff"/>
  <polygon points="1200,1128 560,1260 1200,1122" fill="#ffffff"/>
</svg>
<h2 class="abs head" style="left:115px;top:1513px">Our Services<span class="dash"></span></h2>
<div class="svc" style="left:115px;top:1632px;background:linear-gradient(160deg,#7a5a44,#b98c62 60%,#e38b36)" role="img" aria-label="Two site managers in hard hats pointing at a building under construction"><div class="tag">Preconstruction</div></div>
<div class="svc" style="left:364px;top:1588px;background:linear-gradient(170deg,#e8b822,#efeae2 45%,#cfcfcf)" role="img" aria-label="Yellow hard hat resting on construction drawings beside a tablet"><div class="tag">Estimating</div></div>
<div class="svc" style="left:616px;top:1539px;background:linear-gradient(170deg,#4a8a6a,#3a3f4a 55%,#c65a2a)" role="img" aria-label="Worker in safety harness climbing scaffolding"><div class="tag">Safety Management</div></div>
<div class="svc" style="left:866px;top:1436px;background:linear-gradient(180deg,#8aa3c0,#e9a447 60%,#3d3a3a)" role="img" aria-label="Team of builders beside a tower crane at sunset"><div class="tag">Quality Control</div></div>
<div class="arrow" style="left:44px;top:1763px">‹</div>
<div class="arrow" style="left:1122px;top:1557px">›</div>

<!-- experience -->
<h2 class="abs head" style="left:0;width:1200px;text-align:center;top:2070px;color:#fff"><span class="dash"></span>Our Experience<span class="dash"></span></h2>
<div class="exp" style="left:77px;top:2181px">Quickly mobilize<br>assets + personnel
  <svg width="52" height="56" viewBox="0 0 52 56" fill="none" stroke="#fff" stroke-width="2.5"><rect x="12" y="3" width="26" height="48" rx="4"/><circle cx="25" cy="44" r="2"/><path d="M20 20h14l-4-4M32 30H18l4 4"/></svg></div>
<div class="exp" style="left:347px;top:2181px">Commitment to Value<br>engineering quality
  <svg width="56" height="56" viewBox="0 0 56 56" fill="none" stroke="#fff" stroke-width="2.5"><circle cx="28" cy="28" r="11"/><path d="M28 5v8M28 43v8M5 28h8M43 28h8M12 12l6 6M38 38l6 6M44 12l-6 6M18 38l-6 6"/><circle cx="28" cy="28" r="4"/></svg></div>
<div class="exp" style="left:620px;top:2181px">Qualified field
  <svg width="56" height="56" viewBox="0 0 56 56" fill="none" stroke="#fff" stroke-width="2.5" style="margin-top:18px"><path d="M28 4l6 5 8-1 2 8 7 4-3 8 3 8-7 4-2 8-8-1-6 5-6-5-8 1-2-8-7-4 3-8-3-8 7-4 2-8 8 1z"/><path d="M20 28l6 6 11-12"/></svg></div>
<div class="exp" style="left:891px;top:2181px">Value engineering
  <svg width="52" height="60" viewBox="0 0 52 60" fill="none" stroke="#fff" stroke-width="2.5" style="margin-top:18px"><circle cx="26" cy="38" r="19"/><path d="M26 2v12M20 8l6-6 6 6"/><path d="M21 29h8a4 4 0 010 8h-8zM21 37h9a4 4 0 010 8h-9zM21 29v16"/></svg></div>

<!-- testimonials -->
<svg class="abs" style="left:0;top:2840px" width="1200" height="200" viewBox="0 0 1200 200" aria-hidden="true">
  <defs><linearGradient id="testBand" x1="0" x2="1"><stop offset="0" stop-color="#e2531c"/><stop offset="1" stop-color="#e2b414"/></linearGradient></defs>
  <polygon points="0,0 1200,0 1200,0 0,175" fill="#f4f4f4"/>
  <polygon points="0,175 682,42 0,196" fill="url(#testBand)"/>
</svg>
<div class="abs" style="left:0;top:2550px;width:1200px;height:290px;background:var(--mist)"></div>
<h2 class="abs head" style="left:115px;top:2577px">Our Testimonials<span class="dash"></span></h2>
<div class="quote" style="left:128px;top:2711px"><b style="margin-left:0">Dana Reyes</b><span class="stars">★★★★★</span><p>Lorem ipsum dolor sit amet, etur adipiscing elit, sed do eiusmod tempor incididun</p></div>
<div class="avatar" role="img" aria-label="Client portrait" style="left:98px;top:2741px"></div>
<div class="quote lift" style="left:476px;top:2643px"><b>Dana Reyes</b><span class="stars">★★★★★</span><p>Lorem ipsum dolor sit amet, etur adipiscing elit, sed do eiusmod tempor incididun</p></div>
<div class="avatar" role="img" aria-label="Client portrait" style="left:444px;top:2673px"></div>
<div class="quote" style="left:822px;top:2575px"><b>Dana Reyes</b><span class="stars">★★★★★</span><p>Lorem ipsum dolor sit amet, etur adipiscing elit, sed do eiusmod tempor incididun</p></div>
<div class="avatar" role="img" aria-label="Client portrait" style="left:790px;top:2605px"></div>
<div class="arrow" style="left:44px;top:2810px">‹</div>
<div class="arrow" style="left:1122px;top:2603px">›</div>

<!-- projects -->
<h2 class="abs head" style="left:0;width:1200px;text-align:center;top:2993px"><span class="dash"></span>Our Projects<span class="dash"></span></h2>
<div class="photo" role="img" aria-label="Engineer in hard hat and orange vest on site" style="left:44px;top:3087px;width:269px;height:273px;background:linear-gradient(160deg,#d6d2c8,#8a8f8e 50%,#d76b2a)"></div>
<div class="photo" role="img" aria-label="Construction team in safety vests standing together" style="left:327px;top:3087px;width:269px;height:273px;background:linear-gradient(160deg,#b8b0a2,#c6c93a 55%,#4a4a4a)"></div>
<div class="photo" role="img" aria-label="Crew inspecting a dusty excavation site" style="left:607px;top:3087px;width:269px;height:273px;background:linear-gradient(180deg,#c9d2d9,#b49a7a 55%,#7d6a55)"></div>
<div class="photo" role="img" aria-label="Builders reviewing plans on a rooftop at sunset" style="left:887px;top:3087px;width:269px;height:273px;background:linear-gradient(170deg,#d8b59a,#c98d5c 50%,#5a4a3e)"></div>
<div class="btn" style="left:532px;top:3418px;width:134px">LEARN MORE <i></i></div>

<!-- contact -->
<div class="abs" style="left:0;top:3537px;width:1200px;height:968px;background:var(--mist)"></div>
<h2 class="abs head" style="left:0;width:1200px;text-align:center;top:3615px"><span class="dash"></span>Contact Us<span class="dash"></span></h2>
<div class="field" style="left:222px;top:3718px;width:369px;height:44px;padding-top:16px">NAME</div>
<div class="field" style="left:222px;top:3780px;width:369px;height:44px;padding-top:16px">EMAIL</div>
<div class="field" style="left:222px;top:3841px;width:369px;height:44px;padding-top:16px">PHONE</div>
<div class="field" style="left:607px;top:3718px;width:369px;height:168px;border-radius:24px">MESSAGE</div>
<div class="btn" style="left:530px;top:3927px;width:135px">SUBMIT</div>

<!-- footer -->
<svg class="abs" style="left:0;top:3950px" width="1200" height="555" viewBox="0 0 1200 555" aria-hidden="true">
  <defs><linearGradient id="footBand" x1="0" x2="1"><stop offset="0" stop-color="#e2531c"/><stop offset="1" stop-color="#e2b414"/></linearGradient></defs>
  <polygon points="0,220 1165,12 1165,0 0,210" fill="url(#footBand)"/>
  <polygon points="0,230 1200,12 1200,555 0,555" fill="#000"/>
  <polygon points="0,215 1165,5 1165,22 0,235" fill="url(#footBand)"/>
</svg>
<div class="abs" style="left:118px;top:4270px;width:160px;text-align:center;color:#fff">
  <div style="font-family:'Roboto Condensed',sans-serif;font-weight:800;font-size:28px;line-height:1.05">R W<br>BUILDERS</div>
  <div style="font-size:12px;font-weight:700;margin-top:6px">OAKRIDGE, CA</div>
</div>
<div class="fcol" style="left:397px;top:4222px"><h4>CONTACT</h4>hello@rwbuilders.example<br>(555) 014-2290<br>P.O. Box 4120<br>Oakridge, CA 90210</div>
<div class="fcol" style="left:689px;top:4222px"><h4>QUICK LINKS</h4>Home<br>Services<br>About<br>Testimonial<br>Contact</div>
<div class="fcol" style="left:946px;top:4222px"><h4>OTHER LINKS</h4>FAQ<br>Clients<br>Projects<br>Special Service<br>Media</div>
<div class="abs" style="left:0;width:1200px;top:4447px;text-align:center;color:#fff;font-size:12px">Copyright@2024 - All Rights Reserved By R W Builders</div>

</body>
</html>
```